Business Card front and back

I am looking for business card design. I really really like the design file I uploaded named 627788_19250069_3478263_85f427ee_image

Target Market(s)

Corporate Fitness High end Private country club

Industry/Entity Type

Fitness Industry

Contact Information for Business Card

The last image I like as an example I uploaded a bunch of my logos. The file labeled "the signature" is my business card information for you to use

Colors
0054AA
0677BA
7BADD7
CADEEF
E8F1F8

Requirements
Must have
• E-mail sigThe file I uploaded labeled "627788_19250069_3478263_85f427ee_image" with all the plus signs on the back if those could be the logo symbol I uploaded labeled "1 back.png"

```html
<!DOCTYPE html>
<html lang="en">
<head>
<meta charset="utf-8">
<title>Stride Works – Business Card Front and Back</title>
<link href="https://fonts.googleapis.com/css2?family=Ubuntu:wght@400;500;700&display=swap" rel="stylesheet">
<style>
  :root {
    --stage: #2b2b2c;
    --card: #151516;
    --card-edge: #1d1d1f;
    --white: #ffffff;
    --blue: #4a86cf;
    --muted: #e6e6e6;
    --pattern-dark: #0f0f10;
    --pattern-light: #4a4a4c;
  }
  * { box-sizing: border-box; margin: 0; padding: 0; }
  html, body {
    width: 1200px; height: 900px; overflow: hidden;
    background: var(--stage);
    font-family: "Ubuntu", sans-serif;
  }
  .canvas { position: relative; width: 1200px; height: 900px; }
  .card {
    position: absolute; left: 280px;
    width: 640px; height: 366px;
    background: var(--card);
    border: 1px solid var(--card-edge);
    box-shadow: 0 18px 40px rgba(0,0,0,.55);
    overflow: hidden;
  }
  .card--back { top: 60px; }
  .card--front { top: 470px; }

  /* back */
  .back-pattern {
    position: absolute; inset: 0;
    background: linear-gradient(120deg, var(--pattern-dark) 0%, #1e1e20 45%, var(--pattern-light) 100%);
  }
  .back-brand {
    position: absolute; right: 70px; bottom: 72px;
    display: flex; align-items: center; gap: 12px;
  }
  .brand-square { width: 22px; height: 22px; background: var(--white); }
  .brand-name {
    font-weight: 700; font-size: 26px; letter-spacing: 2px;
    color: var(--white); text-transform: uppercase; white-space: nowrap;
  }

  /* front */
  .front-decor {
    position: absolute; right: 30px; top: 50px;
    width: 300px; height: 270px;
    background: radial-gradient(ellipse at 80% 30%, #4a4a4c 0%, #222224 55%, var(--card) 100%);
    border-radius: 6px;
  }
  .front-brand { position: absolute; left: 40px; top: 36px; font-size: 28px; }
  .person { position: absolute; left: 40px; top: 118px; padding-left: 22px; }
  .person::before {
    content: ""; position: absolute; left: 0; top: 2px;
    width: 10px; height: 40px; background: var(--blue);
  }
  .person-name {
    font-weight: 500; font-size: 26px; color: var(--blue);
    text-transform: uppercase; letter-spacing: .5px; line-height: 1; white-space: nowrap;
  }
  .person-role {
    font-size: 15px; color: var(--muted);
    text-transform: uppercase; letter-spacing: 1px; margin-top: 4px;
  }
  .contact { position: absolute; left: 58px; top: 200px; list-style: none; }
  .contact-item {
    display: flex; align-items: center; gap: 10px;
    font-size: 18px; color: var(--muted); height: 30px; white-space: nowrap;
  }
  .contact-item svg { width: 16px; height: 16px; fill: var(--blue); flex: none; }
</style>
</head>
<body>
<main class="canvas">

  <section class="card card--back" aria-label="Card back">
    <div class="back-pattern" role="img" aria-label="Repeating brand symbol pattern on dark background"></div>
    <div class="back-brand">
      <span class="brand-square"></span>
      <span class="brand-name">Stride Works</span>
    </div>
  </section>

  <section class="card card--front" aria-label="Card front">
    <div class="front-decor" role="img" aria-label="Large faint brand symbol decoration"></div>
    <div class="front-brand brand-name">Stride Works</div>

    <div class="person">
      <p class="person-name">Dana Whitlock</p>
      <p class="person-role">Consultant</p>
    </div>

    <ul class="contact">
      <li class="contact-item">
        <svg viewBox="0 0 24 24"><path d="M6.6 10.8a15 15 0 0 0 6.6 6.6l2.2-2.2c.3-.3.7-.4 1-.2 1.1.4 2.3.6 3.6.6.6 0 1 .4 1 1V20c0 .6-.4 1-1 1A17 17 0 0 1 3 4c0-.6.4-1 1-1h3.5c.6 0 1 .4 1 1 0 1.3.2 2.5.6 3.6.1.3 0 .7-.2 1z"/></svg>
        555-014-2290
      </li>
      <li class="contact-item">
        <svg viewBox="0 0 24 24"><path d="M2 5h20v14H2z M2 5l10 8 10-8" stroke="#151516" stroke-width="1.5"/></svg>
        dana@strideworks.co
      </li>
      <li class="contact-item">
        <svg viewBox="0 0 24 24"><circle cx="12" cy="12" r="10"/><path d="M2 12h20M12 2c3 3 3 17 0 20M12 2c-3 3-3 17 0 20" stroke="#151516" stroke-width="1.3" fill="none"/></svg>
        www.strideworks.co
      </li>
      <li class="contact-item">
        <svg viewBox="0 0 24 24"><path d="M12 2a7 7 0 0 0-7 7c0 5 7 13 7 13s7-8 7-13a7 7 0 0 0-7-7zm0 9.5a2.5 2.5 0 1 1 0-5 2.5 2.5 0 0 1 0 5z"/></svg>
        OR. WA. ID. MT. WY. UT
      </li>
    </ul>
  </section>

</main>
</body>
</html>
```